Brief 1.
An Overview / Background of the Business & Services-
It is a new business being set up. Our business is to design a solution to enable Alumni of higher institutions in Nigeria apply for their academic transcript through our system. the name of our product will be Record Relay Nigeria. We need logo, site banner, advert banner and several academic images. See www.rrly-ng.example for more insight.
The Target Market / Audience you are trying to reach-
Alumni of Nigeria Universities, usually between the ages of 20-40.
Design Specifics; any preferences or ideas for Style, Colour, Imagery, etc-
Color scheme will be several shades of light blue and white. Please check www.rrly-ng.example for more insight.

Brief 2

Pantrybasket.com is an online food and grocery shop, we supply fresh food stuff and other daily essential needs on request to customers. The site is already up (www.pantrybasket.example). We need logo, site rolling banner, advert banner and several offer graphics as shown in the placeholder images in the site now.
Working women in Nigeria.
Color scheme will be several shades of light Green and White. Please check the site.

```html
<!DOCTYPE html>
<html lang="en">
<head>
<meta charset="utf-8">
<title>Pantry Basket – Fresh Food Online</title>
<link rel="stylesheet" href="https://fonts.googleapis.com/css2?family=Open+Sans:wght@400;600;700;800&display=swap">
<style>
:root{
  --green:#7cc242;
  --green-dark:#5c9e2b;
  --green-deep:#4a8522;
  --green-foot:#86c440;
  --green-bar:#5f9a2f;
  --ink:#333;
  --muted:#888;
  --line:#dcdcdc;
  --panel:#f6f6f6;
  --white:#fff;
}
*{box-sizing:border-box;margin:0;padding:0}
html,body{width:711px;height:1200px;overflow:hidden}
body{font-family:"Open Sans",Arial,sans-serif;color:var(--ink);background:var(--white);position:relative;font-size:9px}
.abs{position:absolute}

/* header */
.brand{left:40px;top:22px;display:flex;align-items:center;gap:8px}
.brand .mark{width:28px;height:28px;background:var(--green);border-radius:4px}
.brand .name{font-size:24px;font-weight:700;color:var(--green-dark);letter-spacing:-.3px}
.toplinks{right:41px;top:8px;font-size:8px;color:var(--muted)}
.toplinks span{margin-left:6px}
.search{left:280px;top:36px;width:150px;height:20px;border:1px solid var(--line);border-radius:3px;font-size:8px;color:#aaa;padding:4px 6px;display:flex;justify-content:space-between}
.cart{right:41px;top:36px;width:64px;height:20px;background:var(--green);color:#fff;border-radius:3px;font-size:8px;font-weight:600;display:flex;align-items:center;justify-content:center;gap:4px}

/* nav */
.nav{left:40px;top:78px;width:630px;height:26px;background:var(--green);display:flex}
.nav a{color:#fff;font-size:9.5px;font-weight:700;text-decoration:none;padding:0 14px;line-height:26px}
.nav a.active{background:var(--green-deep)}

/* hero */
.hero{left:40px;top:110px;width:630px;height:200px;background:linear-gradient(90deg,#f4f8ef,#ffffff 60%);border:1px solid #eee;overflow:hidden}
.hero h1{position:absolute;left:28px;top:50px;font-size:27px;font-weight:700;color:var(--green-dark)}
.hero .sub{position:absolute;left:28px;top:86px;font-size:12px;color:var(--green);font-weight:600}
.hero .body{position:absolute;left:28px;top:106px;width:190px;font-size:8px;color:var(--muted);line-height:1.4}
.hero .photo{position:absolute;left:300px;top:0;width:330px;height:200px;background:radial-gradient(circle at 45% 55%,#f7941d,#f26b1d 40%,#e9efe0 75%)}
.dots{position:absolute;left:28px;top:170px;display:flex;gap:4px}
.dots i{width:6px;height:6px;border-radius:50%;background:#ccc}
.dots i:first-child{background:var(--green)}

/* sidebar */
.side-head{background:var(--green);color:#fff;font-size:13px;font-weight:700;padding:4px 10px;border-radius:3px 3px 0 0}
.cats{left:40px;top:355px;width:150px}
.cats ul{list-style:none;border:1px solid var(--line);border-top:0;padding:4px 10px}
.cats li{font-size:7.5px;line-height:13px;color:#555}
.cats li::before{content:"›";color:var(--green);margin-right:5px;font-weight:700}
.best{left:40px;top:490px;width:150px}
.best .list{border:1px solid var(--line);border-top:0;padding:4px 8px}
.item{display:flex;gap:7px;padding:4px 0;border-bottom:1px solid #eee}
.item:last-child{border:0}
.item .thumb{width:34px;height:26px;border-radius:2px;background:linear-gradient(135deg,#e8522a,#f5a623)}
.item .name{font-size:8px;font-weight:600}
.item .price{font-size:7.5px;color:var(--muted)}
.item .add{display:inline-block;background:var(--green);color:#fff;font-size:6px;padding:1px 5px;border-radius:2px;margin-top:1px}
.ad-side{left:40px;top:648px;width:150px;height:110px;background:linear-gradient(160deg,#2a5c8a,#8a6a3a 60%,#d9c39a)}

/* main */
.tiles{left:205px;top:355px;width:465px;display:flex;gap:7px}
.tile{flex:1;height:92px;position:relative;overflow:hidden}
.tile .label{position:absolute;left:0;bottom:0;width:100%;background:rgba(92,158,43,.9);color:#fff;font-size:8.5px;font-weight:600;padding:4px 6px}
.t1{background:linear-gradient(135deg,#e7cdb0,#c98a5a)}
.t2{background:linear-gradient(135deg,#7ab648,#d9423a 70%)}
.t3{background:linear-gradient(135deg,#c8b79a,#6f8a3a)}
.feat-title{left:205px;top:458px;font-size:15px;font-weight:600;color:#444}
.grid{left:205px;top:482px;width:465px;display:grid;grid-template-columns:repeat(3,1fr);gap:8px 7px}
.card{border:1px solid var(--line);height:100px;position:relative}
.card .pic{height:60px;margin:4px}
.card .pname{position:absolute;left:8px;top:70px;font-size:8px}
.card .pprice{position:absolute;left:8px;top:82px;font-size:9px;font-weight:700}
.card svg{position:absolute;right:8px;top:72px}
.fish{background:linear-gradient(90deg,#fff,#9aa3a6 40%,#c7ccc9 60%,#fff)}
.fish2{background:linear-gradient(90deg,#fff,#6f7d72 40%,#8e9a90 60%,#fff)}
.apple{background:radial-gradient(circle,#d81f26 22%,#fff 26%)}
.meat{background:radial-gradient(ellipse,#c2473a 35%,#fff 45%)}
.berry{background:radial-gradient(ellipse,#7a1530 20%,#c0283a 35%,#fff 50%)}
.ad-main{left:205px;top:695px;width:465px;height:64px;background:linear-gradient(90deg,#fff3c4,#f7c948 40%,#e45b2a 70%,#8fbf3a)}

/* service strip */
.strip{left:0;top:785px;width:711px;height:52px;border-top:1px solid #eee;border-bottom:1px solid #eee;display:flex;justify-content:center;gap:40px;align-items:center}
.serv{display:flex;align-items:center;gap:8px}
.serv b{display:block;font-size:11px;font-weight:700;color:#555}
.serv small{font-size:7.5px;color:var(--muted)}

/* footer */
.footer{left:0;top:850px;width:711px;height:322px;background:linear-gradient(180deg,var(--green-foot),var(--green-dark));color:#fff}
.cols{position:absolute;left:40px;top:30px;width:630px;display:flex;justify-content:space-between}
.col h4{font-size:9.5px;font-weight:700;margin-bottom:8px}
.col p{font-size:7px;line-height:14px;opacity:.92}
.social{display:flex;gap:5px}
.social i{width:16px;height:16px;border-radius:50%;background:#fff;opacity:.9}
.pay{display:flex;gap:4px;margin-top:6px}
.pay i{width:20px;height:13px;background:#fff;opacity:.9;border-radius:2px}
.bottom{left:0;top:1172px;width:711px;height:28px;background:var(--green-bar);color:#e8f3dc;font-size:7.5px;padding:9px 40px}
</style>
</head>
<body>

<header>
  <div class="abs brand"><span class="mark"></span><span class="name">Pantry Basket</span></div>
  <div class="abs toplinks"><span>My Account</span> | <span>My Cart</span> | <span>Shop Now</span> | <span>Contact Us</span></div>
  <div class="abs search"><span>Search here...</span><span>⌕</span></div>
  <div class="abs cart">
    <svg width="9" height="9" viewBox="0 0 10 10"><path d="M1 2h2l1.2 5h4.3L10 3H4" fill="none" stroke="#fff" stroke-width="1.2"/></svg>0 items
  </div>
</header>

<nav class="abs nav">
  <a class="active">HOME</a><a>HEALTH &amp; WELLNESS</a><a>FRUITS &amp; VEGS</a><a>POULTRY, MEAT &amp; FISH</a><a>FOOD STUFFS</a><a>RECIPES</a>
</nav>

<section class="abs hero">
  <h1>Premmium Quality</h1>
  <div class="sub">Suspendisse vulputate aliquam</div>
  <p class="body">Etiam est nunc venenatis in tristique eu imperdiet ac nisl cum sociis natoque penatibus.</p>
  <div class="dots"><i></i><i></i><i></i></div>
  <div class="photo" role="img" aria-label="Fresh oranges with green leaves"></div>
</section>

<aside class="abs cats">
  <div class="side-head">Categories</div>
  <ul>
    <li>HEALTH &amp; WELLNESS</li><li>FRUITS &amp; VEG</li><li>POULTRY, MEAT &amp; FISH</li><li>FOOD STUFFS</li><li>RECIPES</li><li>OTHERS</li>
  </ul>
</aside>

<aside class="abs best">
  <div class="side-head">Best Sellings</div>
  <div class="list">
    <div class="item"><div class="thumb" role="img" aria-label="Product photo"></div><div><div class="name">Product Name</div><div class="price">$1,400</div><span class="add">ADD TO CART</span></div></div>
    <div class="item"><div class="thumb" role="img" aria-label="Product photo"></div><div><div class="name">Product Name</div><div class="price">$1,400</div><span class="add">ADD TO CART</span></div></div>
    <div class="item"><div class="thumb" role="img" aria-label="Product photo"></div><div><div class="name">Product Name</div><div class="price">$1,400</div><span class="add">ADD TO CART</span></div></div>
    <div class="item"><div class="thumb" role="img" aria-label="Product photo"></div><div><div class="name">Product Name</div><div class="price">$1,400</div><span class="add">ADD TO CART</span></div></div>
  </div>
</aside>

<div class="abs ad-side" role="img" aria-label="Advert for Lakeside Retreat resort properties"></div>

<section class="abs tiles">
  <div class="tile t1" role="img" aria-label="Health and wellness foods"><span class="label">Health &amp; Wellness</span></div>
  <div class="tile t2" role="img" aria-label="Fresh fruits and vegetables"><span class="label">Fresh Fruits &amp; Veg.</span></div>
  <div class="tile t3" role="img" aria-label="Cooking with herbs"><span class="label">Herbals &amp; Recipes</span></div>
</section>

<h2 class="abs feat-title">Featured Products</h2>
<section class="abs grid">
  <div class="card"><div class="pic fish" role="img" aria-label="Whole fish"></div><div class="pname">Product Name</div><div class="pprice">$255.00</div><svg width="16" height="16" viewBox="0 0 16 16"><rect x="2" y="5" width="12" height="10" rx="2" fill="none" stroke="#7cc242" stroke-width="1.6"/><path d="M5 6V4a3 3 0 0 1 6 0v2" fill="none" stroke="#7cc242" stroke-width="1.6"/></svg></div>
  <div class="card"><div class="pic fish2" role="img" aria-label="Fresh tilapia"></div><div class="pname">Product Name</div><div class="pprice">$255.00</div><svg width="16" height="16" viewBox="0 0 16 16"><rect x="2" y="5" width="12" height="10" rx="2" fill="none" stroke="#7cc242" stroke-width="1.6"/><path d="M5 6V4a3 3 0 0 1 6 0v2" fill="none" stroke="#7cc242" stroke-width="1.6"/></svg></div>
  <div class="card"><div class="pic apple" role="img" aria-label="Red apple"></div><div class="pname">Product Name</div><div class="pprice">$255.00</div><svg width="16" height="16" viewBox="0 0 16 16"><rect x="2" y="5" width="12" height="10" rx="2" fill="none" stroke="#7cc242" stroke-width="1.6"/><path d="M5 6V4a3 3 0 0 1 6 0v2" fill="none" stroke="#7cc242" stroke-width="1.6"/></svg></div>
  <div class="card"><div class="pic meat" role="img" aria-label="Raw meat cuts"></div><div class="pname">Product Name</div><div class="pprice">$255.00</div><svg width="16" height="16" viewBox="0 0 16 16"><rect x="2" y="5" width="12" height="10" rx="2" fill="none" stroke="#7cc242" stroke-width="1.6"/><path d="M5 6V4a3 3 0 0 1 6 0v2" fill="none" stroke="#7cc242" stroke-width="1.6"/></svg></div>
  <div class="card"><div class="pic fish" role="img" aria-label="Fresh mackerel"></div><div class="pname">Product Name</div><div class="pprice">$255.00</div><svg width="16" height="16" viewBox="0 0 16 16"><rect x="2" y="5" width="12" height="10" rx="2" fill="none" stroke="#7cc242" stroke-width="1.6"/><path d="M5 6V4a3 3 0 0 1 6 0v2" fill="none" stroke="#7cc242" stroke-width="1.6"/></svg></div>
  <div class="card"><div class="pic berry" role="img" aria-label="Mixed berries"></div><div class="pname">Product Name</div><div class="pprice">$255.00</div><svg width="16" height="16" viewBox="0 0 16 16"><rect x="2" y="5" width="12" height="10" rx="2" fill="none" stroke="#7cc242" stroke-width="1.6"/><path d="M5 6V4a3 3 0 0 1 6 0v2" fill="none" stroke="#7cc242" stroke-width="1.6"/></svg></div>
</section>

<div class="abs ad-main" role="img" aria-label="Advert for freeze-dried fruits and vegetables"></div>

<section class="abs strip">
  <div class="serv">
    <svg width="26" height="20" viewBox="0 0 26 20"><rect x="1" y="4" width="14" height="10" fill="#7cc242"/><path d="M15 7h6l4 4v3H15z" fill="#7cc242"/><circle cx="6" cy="16" r="2.5" fill="#5c9e2b"/><circle cx="20" cy="16" r="2.5" fill="#5c9e2b"/></svg>
    <div><b>FREE SHIPPING</b><small>On Order over $30 after today</small></div>
  </div>
  <div class="serv">
    <svg width="20" height="20" viewBox="0 0 20 20"><path d="M4 2l4 1 1 4-2 2a10 10 0 0 0 4 4l2-2 4 1 1 4-2 2C9 18 2 11 2 4z" fill="#7cc242"/></svg>
    <div><b>GIVE US CALL NOW</b><small>1-800-555-0142</small></div>
  </div>
  <div class="serv">
    <svg width="22" height="20" viewBox="0 0 22 20"><rect x="2" y="7" width="18" height="12" fill="#7cc242"/><rect x="1" y="4" width="20" height="4" fill="#5c9e2b"/><rect x="10" y="4" width="2" height="15" fill="#fff"/></svg>
    <div><b>FREE DELIVERY &amp; 10% DISCOUNT</b><small>On every Registered Users</small></div>
  </div>
</section>

<footer class="abs footer">
  <div class="cols">
    <div class="col"><h4>COMPANY</h4><p>ABOUT US<br>CAREERS<br>NEWS ROOM<br>BLOG<br>SITEMAP</p></div>
    <div class="col"><h4>FEATURES PRODUCTS</h4><p>FRESH FRUIT PACKS<br>ORGANIC VEGETABLES<br>DAIRY &amp; EGGS<br>MEAT &amp; SEAFOOD<br>PANTRY STAPLES</p></div>
    <div class="col"><h4>RESOURCES</h4><p>ORDER &amp; DELIVERY POLICY<br>INTERNATIONAL DELIVERY<br>CONTACT US<br>SUPPORT<br>TESTIMONIALS</p></div>
    <div class="col"><h4>SUPPORT</h4><p>BUSINESS FAQ<br>MY ORDER STATUS<br>REFUND POLICY<br>RETURN POLICY<br>TERMS OF USE</p></div>
    <div class="col"><h4>GET IN TOUCH</h4>
      <div class="social"><i></i><i></i><i></i><i></i></div>
      <p style="margin-top:8px">We accept</p>
      <div class="pay"><i></i><i></i><i></i><i></i></div>
    </div>
  </div>
</footer>
<div class="abs bottom">© 2014 Pantrybasket.com. All rights reserved. Terms of Use</div>

</body>
</html>
```